Business Card Design Project

i need a bussines car design
Velora Clinical Hypnotherapy

Daniel Wexford
Psychotherapy & Hypnosis

84261937 /0427591628

back of the card appoinment space.

file was provided on a PDF, LOgo , use the blu colorsa as well , elegant, clear,

Target Market(s)

young professional, caucasian , young mothers.

Industry/Entity Type

Business

```html
<!DOCTYPE html>
<html lang="en">
<head>
<meta charset="utf-8">
<title>Velora Hypnotherapy – Business Card</title>
<link rel="stylesheet" href="https://fonts.googleapis.com/css2?family=Questrial&family=Roboto+Condensed:wght@400;700&family=Open+Sans:wght@400;700&display=swap">
<style>
  :root{
    --bg:#dcdcdc;
    --card:#ffffff;
    --blue:#2f78c4;
    --blue-light:#7eb2e4;
    --ink:#333333;
    --ink-soft:#555555;
    --rule:#444444;
  }
  *{box-sizing:border-box;margin:0;padding:0}
  html,body{width:1200px;height:900px;overflow:hidden}
  body{background:radial-gradient(circle at 50% 45%,#f1f1f1 0%,var(--bg) 80%);position:relative;font-family:"Questrial",sans-serif}

  .card{position:absolute;background:var(--card);box-shadow:0 6px 18px rgba(0,0,0,.18)}

  /* Front */
  .card-front{left:70px;top:260px;width:620px;height:379px;overflow:hidden}
  .brand{position:absolute;left:120px;top:58px;display:flex;align-items:center;gap:14px}
  .brand-dot{width:34px;height:34px;border-radius:50%;background:var(--blue)}
  .brand-name{font-size:38px;color:var(--blue);letter-spacing:.5px;line-height:1}
  .brand-web{position:absolute;left:168px;top:104px;width:400px;border-top:1.5px solid var(--blue);padding-top:4px;font-size:13px;letter-spacing:2.4px;color:var(--ink)}
  .person{position:absolute;right:44px;top:160px;text-align:right}
  .person-name{font-family:"Open Sans",sans-serif;font-weight:700;font-size:20px;color:var(--ink);letter-spacing:.5px}
  .person-role{font-size:17px;color:var(--ink-soft);margin-top:1px}
  .contacts{position:absolute;right:44px;top:234px;text-align:right;font-size:17px;color:var(--ink);line-height:1.3}
  .contacts b{font-family:"Open Sans",sans-serif;font-weight:700;font-size:15px}
  .clinic{position:absolute;left:40px;top:286px;font-family:"Open Sans",sans-serif;color:var(--blue)}
  .clinic-label{font-weight:700;font-size:16px;margin-left:118px}
  .clinic-address{font-family:"Questrial",sans-serif;font-size:20px;margin-top:2px}
  .band{position:absolute;left:0;right:0;bottom:0;height:16px;background:linear-gradient(90deg,var(--blue) 0%,var(--blue-light) 100%)}

  /* Back */
  .card-back{left:750px;top:140px;width:379px;height:620px;padding:36px 30px 30px;font-family:"Roboto Condensed",sans-serif;color:var(--ink)}
  .back-title{font-size:13px;font-weight:700;letter-spacing:2px}
  .back-title span{letter-spacing:1px;font-weight:400}
  .back-info{font-size:14px;line-height:1.55;margin-top:6px}
  .appt-heading{font-size:17px;font-weight:700;margin-top:28px}
  .appt-list{list-style:none;margin-top:14px}
  .appt-row{display:flex;align-items:flex-end;gap:6px;font-size:13px;height:44px;color:var(--ink-soft)}
  .appt-line{flex:1;border-bottom:1px solid var(--rule);height:18px}
  .appt-line.short{flex:0 0 52px}
  .appt-slash{padding-bottom:1px}
  .back-note{position:absolute;left:30px;right:30px;bottom:58px;font-size:10.5px;line-height:1.4;color:var(--ink-soft)}
  .provider{position:absolute;left:30px;bottom:30px;font-size:13px;font-weight:700}
</style>
</head>
<body>

<section class="card card-front" aria-label="Business card front">
  <div class="brand">
    <span class="brand-dot"></span>
    <span class="brand-name">Velora Hypnotherapy</span>
  </div>
  <div class="brand-web">www.veloraclinicalhypnotherapy.com.au</div>

  <div class="person">
    <p class="person-name">DANIEL WEXFORD</p>
    <p class="person-role">Psychotherapy &amp; Hypnosis</p>
  </div>

  <div class="contacts">
    <p><b>Mobile:</b> 842 61 937</p>
    <p><b>Tel:</b> 0427 591 628</p>
  </div>

  <div class="clinic">
    <p class="clinic-label">Clinic Address:</p>
    <p class="clinic-address">142 Harlow Road, Kingsmere</p>
  </div>

  <div class="band"></div>
</section>

<section class="card card-back" aria-label="Business card back">
  <p class="back-title">VELORA <span>Clinical Hypnotherapy</span></p>
  <div class="back-info">
    <p>For appointment · Phone: 0427 591 628</p>
    <p>87 Linden Street, Ashbrook 3021</p>
    <p>info@veloraclinicalhypnotherapy.com.au</p>
  </div>

  <p class="appt-heading">Your Appointments</p>
  <ul class="appt-list">
    <li class="appt-row"><span class="appt-line"></span><span>am/pm</span><span class="appt-line short"></span><span class="appt-slash">/</span><span class="appt-line short"></span></li>
    <li class="appt-row"><span class="appt-line"></span><span>am/pm</span><span class="appt-line short"></span><span class="appt-slash">/</span><span class="appt-line short"></span></li>
    <li class="appt-row"><span class="appt-line"></span><span>am/pm</span><span class="appt-line short"></span><span class="appt-slash">/</span><span class="appt-line short"></span></li>
    <li class="appt-row"><span class="appt-line"></span><span>am/pm</span><span class="appt-line short"></span><span class="appt-slash">/</span><span class="appt-line short"></span></li>
    <li class="appt-row"><span class="appt-line"></span><span>am/pm</span><span class="appt-line short"></span><span class="appt-slash">/</span><span class="appt-line short"></span></li>
  </ul>

  <p class="back-note">To reschedule, please SMS or phone<br>24 hours prior to your time.</p>
  <p class="provider">NPV048215</p>
</section>

</body>
</html>
```